Mailchimp Template Design

We are looking to create two types of email template for use specifically within Mailchimp including a Newsletter Template Layout and a Campaign Template Layout, as such require the templates to be designed in HTML to be compatible with Mailchimp.

The Newsletter Template Layout should accommodate for three newsletter article features and two separate product offer features. Each newsletter article feature should contain: A small image (16:9 ratio), a Feature title and up to 100 words as a short description and each Product offer feature should show a large image (4:3 ratio) and short description of

The Campaign Template Layout should accommodate for one large (4:3 ratio) campaign image, a small description of 50 words and three product offer areas.

The look and feel of the designs should be consistent with the Bramble Co website (www.brambleco.co.uk) and the uploaded source material that is attached to this project brief.
Updates

Project Deadline Extended
Reason: Review of other business marketing efforts to see which design is the most contextually relevant.

Target Market(s)

Pet Owning Consumer

Industry/Entity Type

Pet Shop

Number of Pages Required

2 page

Font styles to use
Other font styles liked:
• Provided in Brief Attachment

Requirements
Must have
• Compatibility with Mail Chimp
• Consistency with Bramble Co (www.brambleco.co.uk) Look & Feel and Brand Guidelines

```html
<!DOCTYPE html>
<html lang="en">
<head>
<meta charset="utf-8">
<title>Bramble Co Newsletter</title>
<link rel="stylesheet" href="https://fonts.googleapis.com/css2?family=Open+Sans:wght@400;600;700&family=Montserrat:wght@300;400&display=swap">
<style>
  :root {
    --page-bg: #e5e5e5;
    --card-bg: #ffffff;
    --brand-blue: #42ace0;
    --text-dark: #555555;
    --text-body: #666666;
    --text-soft: #777777;
    --frame-line: #dddddd;
    --frame-fill: #f2f2f2;
    --price-bg: #e3e3e3;
    --icon-line: #9a9a9a;
  }
  * { box-sizing: border-box; margin: 0; padding: 0; }
  html, body { width: 700px; height: 1200px; overflow: hidden; }
  body { background: var(--page-bg); font-family: "Open Sans", sans-serif; position: relative; }

  .email {
    position: absolute; left: 132px; top: 70px; width: 438px; height: 1015px;
    background: var(--card-bg); border-top: 3px solid var(--brand-blue);
    box-shadow: 0 10px 14px -8px rgba(0,0,0,0.35);
  }
  .brand {
    position: absolute; left: 15px; top: 8px; width: 107px; height: 54px;
    background: var(--brand-blue); display: flex; align-items: center; justify-content: center;
    color: #fff; font-weight: 700; font-size: 16px;
  }
  .issue-date { position: absolute; right: 19px; top: 15px; font-size: 10.5px; font-weight: 600; color: var(--text-dark); }
  .share { position: absolute; right: 19px; top: 33px; display: flex; gap: 4px; }
  .share span { width: 19px; height: 19px; display: block; border-radius: 1px; }
  .share .s1 { background: #3b5998; } .share .s2 { background: #1da1f2; } .share .s3 { background: #e02a2a; }

  .band {
    position: absolute; left: 18px; width: 400px; height: 28px; background: var(--brand-blue);
    color: #fff; font-weight: 700; font-size: 12px; display: flex; align-items: center; justify-content: center;
  }
  .band.featured { top: 92px; } .band.offers { top: 581px; }

  .article { position: absolute; left: 22px; width: 400px; height: 130px; }
  .article.a1 { top: 144px; } .article.a2 { top: 290px; } .article.a3 { top: 438px; }
  .thumb-frame {
    position: absolute; left: 0; top: 0; width: 102px; height: 103px;
    background: var(--frame-fill); border: 1px solid var(--frame-line); padding: 5px;
  }
  .thumb { position: relative; width: 90px; height: 91px; overflow: hidden; }
  .thumb.puppy { background: radial-gradient(circle at 62% 55%, #b9b3a8 0%, #cfd8b0 45%, #dde7c0 100%); }
  .thumb.hedgehog { background: radial-gradient(circle at 58% 50%, #4d4a45 0%, #7e7565 40%, #ac9d80 100%); }
  .thumb.rabbit { background: radial-gradient(circle at 45% 58%, #c9ab8a 0%, #a9bf78 48%, #97c45e 100%); }
  .thumb .date-tag {
    position: absolute; right: 0; bottom: 0; width: 44px; height: 32px; background: var(--brand-blue);
    color: #fff; font-size: 10px; font-weight: 600; display: flex; align-items: center; justify-content: center;
  }
  .article-title { position: absolute; left: 120px; top: -4px; width: 270px; font-size: 11.6px; font-weight: 600; color: var(--text-dark); line-height: 14.5px; }
  .article-text { position: absolute; left: 120px; width: 266px; font-size: 9.2px; color: var(--text-body); line-height: 14.4px; }
  .a1 .article-text, .a3 .article-text { top: 31px; }
  .a2 .article-text { top: 21px; }
  .read-more {
    position: absolute; left: 120px; width: 88px; height: 32px; border: 1px solid var(--frame-line);
    font-size: 9.5px; font-weight: 700; color: var(--text-dark); letter-spacing: 0.3px;
    display: flex; align-items: center; justify-content: center;
  }
  .a1 .read-more, .a3 .read-more { top: 81px; }
  .a2 .read-more { top: 84px; }

  .offer-heading { position: absolute; top: 628px; font-family: "Montserrat", sans-serif; font-weight: 300; font-size: 13.5px; color: #333; }
  .offer-heading.o1 { left: 17px; } .offer-heading.o2 { left: 226px; }
  .offer { position: absolute; top: 656px; width: 195px; height: 162px; border: 1px solid var(--frame-line); }
  .offer.o1 { left: 20px; } .offer.o2 { left: 225px; }
  .offer .pack { position: absolute; left: 8px; top: 9px; width: 72px; height: 104px; box-shadow: 1px 1px 3px rgba(0,0,0,0.2); }
  .offer.o1 .pack { background: linear-gradient(160deg, #ffffff 0%, #f7efe2 35%, #f2b65c 75%, #e8962c 100%); }
  .offer.o2 .pack { left: 33px; width: 52px; background: linear-gradient(170deg, #1f3b8c 0%, #2a5a9f 40%, #3a9aa6 75%, #6bb37a 100%); }
  .offer-name { position: absolute; left: 89px; top: 33px; width: 100px; font-family: "Montserrat", sans-serif; font-weight: 300; font-size: 10.4px; line-height: 13px; color: #444; }
  .offer.o2 .offer-name { left: 95px; top: 46px; }
  .price-row { position: absolute; top: 121px; display: flex; height: 27px; }
  .offer.o1 .price-row { left: 46px; } .offer.o2 .price-row { left: 35px; }
  .price { width: 50px; background: var(--price-bg); color: var(--brand-blue); font-weight: 700; font-size: 12.5px; display: flex; align-items: center; justify-content: center; }
  .basket { width: 43px; background: var(--brand-blue); display: flex; align-items: center; justify-content: center; }

  .footer-social { position: absolute; top: 868px; left: 0; width: 100%; display: flex; justify-content: center; gap: 5px; }
  .footer-social span {
    width: 20px; height: 20px; border: 1.5px solid var(--icon-line); border-radius: 50%; display: block;
    background: radial-gradient(circle, #ffffff 0 38%, #ececec 40% 100%);
  }
  .sender { position: absolute; top: 902px; left: 0; width: 100%; text-align: center; font-size: 9px; line-height: 13px; color: var(--text-soft); }
  .rule { position: absolute; top: 946px; left: 138px; width: 152px; border-top: 1px solid #ccc; }
  .copyright { position: absolute; top: 958px; left: 0; width: 100%; text-align: center; font-size: 10px; color: var(--text-dark); }
</style>
</head>
<body>
<main class="email">
  <header>
    <div class="brand">Bramble Co</div>
    <div class="issue-date">3rd March 2017</div>
    <div class="share"><span class="s1"></span><span class="s2"></span><span class="s3"></span></div>
  </header>

  <div class="band featured">Featured Article:</div>

  <article class="article a1">
    <div class="thumb-frame"><div class="thumb puppy" role="img" aria-label="Illustration of a spotted puppy">
      <span class="date-tag">19Jan</span></div></div>
    <h2 class="article-title">Caring for newly hatched Chicks with The Hen House Society</h2>
    <p class="article-text">After Hatching When chicks are hatching they should be left alone. At first they are wet and look a bit bedraggled. It will take several hours before they move about...</p>
    <a class="read-more">Read More &gt;</a>
  </article>

  <article class="article a2">
    <div class="thumb-frame"><div class="thumb hedgehog" role="img" aria-label="Illustration of a hedgehog">
      <span class="date-tag">19Jan</span></div></div>
    <h2 class="article-title">Identifying Illness in Pond Fish with Aquavia</h2>
    <p class="article-text">Like humans, if fish are weakened or stressed, their ability to fight off infection is compromised. Conditions which can trigger illness in fish include poor water quality, poor diet and...</p>
    <a class="read-more">Read More &gt;</a>
  </article>

  <article class="article a3">
    <div class="thumb-frame"><div class="thumb rabbit" role="img" aria-label="Illustration of a brown rabbit">
      <span class="date-tag">19Jan</span></div></div>
    <h2 class="article-title">Caring for newly hatched Chicks with The Hen House Society</h2>
    <p class="article-text">After Hatching When chicks are hatching they should be left alone. At first they are wet and look a bit bedraggled. It will take several hours before they move about...</p>
    <a class="read-more">Read More &gt;</a>
  </article>

  <div class="band offers">Product Offers</div>

  <h3 class="offer-heading o1">Behavioural Treatments</h3>
  <h3 class="offer-heading o2">Behavioural Treatments</h3>

  <section class="offer o1">
    <div class="pack" role="img" aria-label="Calming tablets product box"></div>
    <p class="offer-name">Calmwell Tablets For Cats and Dogs - Calming Tablets 30pk</p>
    <div class="price-row"><span class="price">£9.18</span><span class="basket">
      <svg width="16" height="13" viewBox="0 0 16 13"><path d="M4 5 L7 1 M12 5 L9 1" stroke="#fff" stroke-width="1.5" fill="none"/><path d="M1 5 H15 L13 12 H3 Z" fill="#fff"/></svg></span></div>
  </section>

  <section class="offer o2">
    <div class="pack" role="img" aria-label="Express calming tablets product box"></div>
    <p class="offer-name">Soothera Express Tablets</p>
    <div class="price-row"><span class="price">£7.06</span><span class="basket">
      <svg width="16" height="13" viewBox="0 0 16 13"><path d="M4 5 L7 1 M12 5 L9 1" stroke="#fff" stroke-width="1.5" fill="none"/><path d="M1 5 H15 L13 12 H3 Z" fill="#fff"/></svg></span></div>
  </section>

  <footer>
    <div class="footer-social"><span></span><span></span><span></span></div>
    <p class="sender">This email was sent by<br>petletters.example. 412 Willow Lane,<br>Millbrook, NC 27000</p>
    <div class="rule"></div>
    <p class="copyright">Copyright © 2017 Company Name.</p>
  </footer>
</main>
</body>
</html>
```